Renny Oskow - Free Personalised Health Consultation - "One size does not fit all"

This flyer will be left on tables/seats at speaking events and seminars and used to attain leads.

Top half will have "SMS me for a FREE Personalised Health Consultation" and my picture (see www.rennyoskow-demo.com and pick most engaging photo) and underneath my contact details. It must have lines with "Notes:" halfway down so people can take notes at the seminar and lines on the back with my contact details again and "Notes: with lines.

I am having a business card also being designed by Artvane for same and would like the flyer and business card to carry a similar feel/look for consistency.

Below is the brief for the business card being designed:
Business Card for www.rennyoskow-demo.com site. It is a trust site and I use it for 1:1 relatable connections. It is the one I use for building intimate 1:1 trust building and Exec Coaching Services and programs for high wealth individuals and corporates. I also have a commercial programmatic site of my personal health products and services and programs for main stream one to many. www.steadyforwardliving-demo.com that can also provoke thought for the www.rennyoskow-demo.com business card. (mind you will get a separate business card for that site, but want to provide context). It has a logo which you may want to draw from in designing the rennyoskow business card which is personal and is about building my brand. There is also a rennyoskow personal PX page and rennyoskow business PX page. I am a Certified Talent Compass 3.1 Coach with Norvik and you can get a corporate brief of me on there to give you more context https://www.norvikcoachhub-demo.com/coach/en-us/directory?search=renny

Target Market(s)

Exec, IT, Health conscious. Corporates wanting to run Health and Wellness programs. Those wanting to go from good to great. Millennials to Middleaged.

Industry/Entity Type

Health And Wellness

Font styles to use
Sans Serif
Other font styles liked:
• Arial and Calibri ok too

Colors

Designer to choose colors to be used in the design.

Requirements
Must have
• Picture of me - use best from www.rennyoskow-demo.com or can send one you choose.
• Contact details like my buisness card being designed by you guys in separate project.
• Name: Renny Oskow
• email: renny@rennyoskow-demo.,com
• Phone: Australia +61 400 000 137 Singapore: +65 9000 2468
Nice to have
• Open to ideas

```html
<!DOCTYPE html>
<html lang="en">
<head>
<meta charset="utf-8">
<title>Renny Oskow – Notes Flyer</title>
<link rel="stylesheet" href="https://fonts.googleapis.com/css2?family=Oswald:wght@600&family=Montserrat:wght@400;500&family=Arimo:wght@400&family=Mr+Dafoe&display=swap">
<style>
  :root {
    --bg: #4b4038;
    --paper: #ffffff;
    --ink: #1e1e1e;
    --panel: #2c2c2c;
    --rule: #b9b9b9;
    --photo-light: #e6e6e6;
    --photo-mid: #9a9a9a;
    --photo-dark: #3a3a3a;
  }
  * { margin: 0; padding: 0; box-sizing: border-box; }
  html, body { width: 1200px; height: 903px; overflow: hidden; background: var(--bg); }
  .canvas { position: relative; width: 1200px; height: 903px; }

  .card {
    position: absolute; top: 142px; width: 362px; height: 620px;
    background: var(--paper); overflow: hidden;
    box-shadow: 0 4px 14px rgba(0,0,0,.35);
  }
  .card--front { left: 210px; }
  .card--back { left: 628px; }

  .hero { position: absolute; left: 0; top: 0; width: 362px; height: 210px; }
  .hero__photo {
    position: absolute; inset: 0;
    background: linear-gradient(90deg, var(--photo-light) 0%, #cfcfcf 45%, var(--photo-mid) 70%, var(--photo-dark) 100%);
  }
  .hero__panel { position: absolute; left: 0; top: 19px; }
  .hero__name {
    position: absolute; left: 44px; top: 32px;
    font-family: "Mr Dafoe", cursive; font-size: 22px; color: #fff; letter-spacing: .5px;
  }
  .hero__headline {
    position: absolute; left: 20px; top: 70px;
    font-family: "Oswald", sans-serif; font-weight: 600; font-size: 18.5px; color: #fff; line-height: 1;
  }
  .hero__email {
    position: absolute; left: 20px; top: 95px;
    font-family: "Montserrat", sans-serif; font-size: 14.5px; color: #fff;
  }
  .hero__offer {
    position: absolute; left: 20px; top: 125px; width: 200px;
    font-family: "Montserrat", sans-serif; font-weight: 500; font-size: 12.2px; line-height: 15.5px; color: #fff;
  }

  .notes { position: absolute; left: 23px; right: 23px; }
  .notes__label {
    font-family: "Montserrat", sans-serif; font-weight: 500; font-size: 10.5px; color: var(--ink); letter-spacing: .3px;
  }
  .notes__lines { position: absolute; left: 0; right: 0; }
  .notes__lines span {
    position: absolute; left: 0; right: 0; height: 0;
    border-top: 1px dotted var(--rule);
  }
  .card--front .notes { top: 222px; bottom: 50px; }
  .card--back .notes { top: 18px; bottom: 30px; }

  .footer { position: absolute; left: 0; bottom: 0; width: 362px; height: 32px; }
  .footer__tagline {
    position: absolute; left: 23px; top: 9px;
    font-family: "Arimo", sans-serif; font-size: 9.6px; color: #fff; white-space: nowrap;
  }
  .footer__url {
    position: absolute; right: 10px; top: 9px;
    font-family: "Arimo", sans-serif; font-size: 9.6px; color: var(--ink); white-space: nowrap;
  }
</style>
</head>
<body>
<div class="canvas">

  <section class="card card--front">
    <div class="hero">
      <div class="hero__photo" role="img" aria-label="Black and white photo of Renny Oskow sitting on a bicycle in a bright street"></div>
      <svg class="hero__panel" width="230" height="175" viewBox="0 0 230 175" aria-hidden="true">
        <polygon points="0,0 206,0 227,87 206,175 0,175" fill="var(--panel)"/>
      </svg>
      <div class="hero__name">Renny Oskow</div>
      <div class="hero__headline">EMAIL ME AT CONNECT</div>
      <div class="hero__email">@rennyoskow-demo.com</div>
      <p class="hero__offer">to connect for a no charge Personalised health goal chat</p>
    </div>

    <div class="notes">
      <div class="notes__label">NOTES</div>
      <div class="notes__lines">
        <span style="top:4px"></span><span style="top:28px"></span><span style="top:52px"></span>
        <span style="top:76px"></span><span style="top:100px"></span><span style="top:124px"></span>
        <span style="top:148px"></span><span style="top:171px"></span><span style="top:195px"></span>
        <span style="top:219px"></span><span style="top:243px"></span><span style="top:267px"></span>
        <span style="top:291px"></span><span style="top:315px"></span>
      </div>
    </div>

    <footer class="footer">
      <svg width="362" height="32" viewBox="0 0 362 32" aria-hidden="true" style="position:absolute;left:0;top:0">
        <rect width="362" height="32" fill="var(--panel)"/>
        <polygon points="234,2 362,2 362,32 226,32" fill="var(--paper)"/>
      </svg>
      <span class="footer__tagline">Health &gt; Performance &gt; Longevity &gt; Wellbeing</span>
      <span class="footer__url">www.rennyoskow-demo.com</span>
    </footer>
  </section>

  <section class="card card--back">
    <div class="notes">
      <div class="notes__label">NOTES</div>
      <div class="notes__lines">
        <span style="top:4px"></span><span style="top:28px"></span><span style="top:52px"></span>
        <span style="top:76px"></span><span style="top:100px"></span><span style="top:124px"></span>
        <span style="top:148px"></span><span style="top:172px"></span><span style="top:196px"></span>
        <span style="top:220px"></span><span style="top:244px"></span><span style="top:268px"></span>
        <span style="top:292px"></span><span style="top:316px"></span><span style="top:340px"></span>
        <span style="top:364px"></span><span style="top:388px"></span><span style="top:412px"></span>
        <span style="top:436px"></span><span style="top:460px"></span><span style="top:484px"></span>
        <span style="top:508px"></span><span style="top:532px"></span>
      </div>
    </div>

    <footer class="footer">
      <svg width="362" height="32" viewBox="0 0 362 32" aria-hidden="true" style="position:absolute;left:0;top:0">
        <rect width="362" height="32" fill="var(--panel)"/>
        <polygon points="234,2 362,2 362,32 226,32" fill="var(--paper)"/>
      </svg>
      <span class="footer__tagline">Health &gt; Performance &gt; Longevity &gt; Wellbeing</span>
      <span class="footer__url">www.rennyoskow-demo.com</span>
    </footer>
  </section>

</div>
</body>
</html>
```